Business Card Design - Photographer

I am a landscape photographer and I require a business card design. 

I require two designs:
1)  a double sided business card
 and
b)  a single sided business card 

The single sided design can either be the same as the double sided (with just one side having all the information)....or it can be an entire new design. Its up to you.

My corporate colours are (CMYK):

Blue   69, 32, 0, 0
Grey  72,  64,  47,  31
Green  32,  2,  91,  0
Yellow   0, 19, 92, 0
Orange  0, 39, 75, 0

Colour space in final file should be in CMYK.

The details that need to be included on the card:

- Use the provided Logo
- Name: Wiktor Baranowski
- Email:   sales@vistalumeworks.com.au
- Website:    vistalumeworks.com.au
- Twitter:    twitter.com/vistalumeworks
- Facebook:   facebook.com/vistalumeworks
- Mobile  0417 539 662

Please use the attached template to design the logo to the specified size, including the marked bleed lines. I have also attached my logo in PNG (transparent background) and ai format for you to use.

The final file should be:
- Photoshop version with layers so I can edit the name/text etc. All non vector files should be high resolution at 1039 x 697 pixels at 300 dpi.

I also require a file as:
- Vector based PDF

Anyway questions please contact me.

Thank you

Industry/Entity Type

Landscape

Logo styles of interest
Pictorial/Combination Logo
Abstract Logo
Wordmark Logo
Lettermark Logo
Requirements
Must have
• The details that need to be included on the card:

- Use the provided Logo
- Name: Wiktor Baranowski
- Email: sales@vistalumeworks.com.au
- Website: vistalumeworks.com.au
- Twitter: twitter.com/vistalumeworks
- Facebook: facebook.com/vistalumeworks
- Mobile 0417 539 662

```html
<!DOCTYPE html>
<html lang="en">
<head>
<meta charset="utf-8">
<title>Vistalume Works — Business Card</title>
<link href="https://fonts.googleapis.com/css2?family=Cinzel:wght@500&family=Tinos&family=Open+Sans:wght@400&display=swap" rel="stylesheet">
<style>
  :root {
    --slate: #42455a;
    --slate-soft: #4c4f63;
    --yellow: #fdc60d;
    --blue: #3f8fd2;
    --paper: #ffffff;
    --ink: #4a4a4a;
    --backdrop: #ecebe8;
  }
  * { margin: 0; padding: 0; box-sizing: border-box; }
  html, body { width: 1200px; height: 1111px; overflow: hidden; background: var(--backdrop); }
  .canvas { position: relative; width: 1200px; height: 1111px; }

  .card { position: absolute; width: 779px; height: 445px; border-radius: 22px; overflow: hidden; }
  .card-front { left: 78px; top: 81px; background: var(--paper); box-shadow: 0 2px 6px rgba(0,0,0,.18); }
  .card-back { left: 333px; top: 581px; background: var(--slate); box-shadow: 0 2px 6px rgba(0,0,0,.18); }

  .front-swoosh { position: absolute; inset: 0; width: 779px; height: 445px; }

  .brand-mark { position: absolute; border-radius: 50%; }
  .card-front .brand-mark { left: 159px; top: 160px; width: 118px; height: 118px; background: var(--slate); }
  .card-back .brand-mark { left: 330px; top: 80px; width: 118px; height: 118px; background: var(--paper); }

  .brand-name {
    position: absolute; width: 440px; text-align: center;
    font-family: "Cinzel", serif; font-weight: 500; font-size: 33px; letter-spacing: 1px;
    white-space: nowrap;
  }
  .card-front .brand-name { left: -2px; top: 296px; color: var(--slate); }
  .card-back .brand-name { left: 170px; top: 228px; color: var(--paper); }

  .divider { position: absolute; left: 428px; top: 186px; width: 1px; height: 204px; background: #c9c9cc; }

  .contact-list { position: absolute; left: 457px; top: 178px; list-style: none;
    font-family: "Tinos", serif; font-size: 19px; color: var(--ink); }
  .contact-list li { display: flex; align-items: center; height: 27.5px; white-space: nowrap; }
  .contact-list svg { width: 12px; height: 12px; margin-right: 7px; flex: none; fill: var(--slate); }

  .address { position: absolute; left: 457px; top: 332px;
    font-family: "Tinos", serif; font-size: 19px; line-height: 27px; color: var(--ink); }

  .back-url { position: absolute; left: 0; width: 779px; top: 363px; text-align: center;
    font-family: "Open Sans", sans-serif; font-size: 18px; letter-spacing: 3.2px; color: var(--paper); }
</style>
</head>
<body>
<main class="canvas">

  <section class="card card-front" aria-label="Card front">
    <svg class="front-swoosh" viewBox="0 0 779 445" aria-hidden="true">
      <path d="M0 0 H779 V176 C610 70 330 22 0 42 Z" fill="var(--slate)"/>
      <path d="M0 40 C320 12 620 62 779 172 V205 C620 95 320 36 0 54 Z" fill="var(--yellow)"/>
      <path d="M0 50 C150 34 300 26 420 28 C300 36 150 48 0 64 Z" fill="var(--blue)"/>
      <circle cx="721" cy="70" r="36" fill="var(--slate-soft)"/>
    </svg>

    <div class="brand-mark" aria-hidden="true"></div>
    <div class="brand-name">Vistalume Works</div>

    <div class="divider"></div>

    <ul class="contact-list">
      <li><svg viewBox="0 0 12 12"><rect x="3" y="0" width="6" height="12" rx="1.2"/><rect x="4.2" y="1.5" width="3.6" height="7" fill="#fff"/></svg>0417 539 662</li>
      <li><svg viewBox="0 0 12 12"><rect x="0" y="2" width="12" height="8"/><path d="M0 2 L6 7 L12 2" fill="none" stroke="#fff" stroke-width="1"/></svg>sales@vistalumeworks.com.au</li>
      <li><svg viewBox="0 0 12 12"><circle cx="6" cy="6" r="5.5"/></svg>www.vistalumeworks.com.au</li>
      <li><svg viewBox="0 0 12 12"><rect x="0" y="0" width="12" height="12" rx="2"/></svg>vistalumeworks</li>
      <li><svg viewBox="0 0 12 12"><rect x="0" y="0" width="12" height="12" rx="2"/></svg>vistalumeworks</li>
    </ul>

    <p class="address">00, Complex Name<br>State Name, City 0020</p>
  </section>

  <section class="card card-back" aria-label="Card back">
    <div class="brand-mark" aria-hidden="true"></div>
    <div class="brand-name">Vistalume Works</div>
    <p class="back-url">www.vistalumeworks.com.au</p>
  </section>

</main>
</body>
</html>
```